The Linen Loft Co

We need a business card design for our wardrobe company.
Please visit our website www.gentlelinenlofts.com to get an idea of who we are.

```html
<!DOCTYPE html>
<html lang="en">
<head>
<meta charset="utf-8">
<title>The Linen Loft Co — Business Card</title>
<link rel="stylesheet" href="https://fonts.googleapis.com/css2?family=Roboto:wght@400;500;700&display=swap">
<style>
  :root {
    --page-bg: #e9e9e9;
    --card-white: #ffffff;
    --ink: #111111;
    --wave-black: #000000;
    --on-dark: #ffffff;
  }
  * { box-sizing: border-box; margin: 0; padding: 0; }
  html, body {
    width: 1200px;
    height: 989px;
    overflow: hidden;
    background: var(--page-bg);
    font-family: "Roboto", Arial, sans-serif;
  }
  .card {
    position: absolute;
    left: 50px;
    top: 177px;
    width: 1100px;
    height: 634px;
    background: var(--card-white);
    overflow: hidden;
    box-shadow: 0 2px 10px rgba(0,0,0,0.18);
  }
  .card-wave {
    position: absolute;
    inset: 0;
    width: 100%;
    height: 100%;
  }
  .brand-mark {
    position: absolute;
    left: 73px;
    top: 136px;
    width: 88px;
    height: 88px;
    border: 3px solid var(--ink);
  }
  .brand-text {
    position: absolute;
    left: 252px;
    top: 146px;
    width: 300px;
    text-align: center;
    color: var(--ink);
  }
  .brand-name {
    font-size: 26px;
    font-weight: 500;
    line-height: 1;
    white-space: nowrap;
  }
  .brand-tagline {
    margin-top: 14px;
    font-size: 21px;
    font-weight: 500;
    line-height: 1;
    white-space: nowrap;
  }
  .contact {
    position: absolute;
    right: 60px;
    top: 350px;
    text-align: right;
    color: var(--on-dark);
  }
  .person-name {
    font-size: 44px;
    font-weight: 700;
    line-height: 1;
  }
  .person-role {
    margin-top: 3px;
    font-size: 28px;
    font-weight: 500;
    line-height: 1;
  }
  .contact-list {
    list-style: none;
    margin-top: 16px;
  }
  .contact-item {
    display: flex;
    justify-content: flex-end;
    align-items: center;
    gap: 16px;
    font-size: 27px;
    font-weight: 400;
    line-height: 34px;
  }
  .contact-icon {
    width: 24px;
    height: 24px;
    flex: none;
  }
  .address {
    margin-top: 8px;
    font-size: 27px;
    font-weight: 400;
    line-height: 34px;
    white-space: nowrap;
  }
</style>
</head>
<body>
  <section class="card">
    <svg class="card-wave" viewBox="0 0 1100 634" aria-hidden="true">
      <path fill="var(--wave-black)" d="M0,480 C120,522 200,545 270,537 C400,522 520,380 640,270 C760,160 880,95 1000,98 C1050,99 1080,105 1100,113 L1100,634 L0,634 Z"/>
      <path fill="none" stroke="var(--card-white)" stroke-width="6" d="M110,548 C180,568 230,577 290,570 C420,556 530,402 652,296 C772,192 900,142 1100,156"/>
    </svg>

    <div class="brand-mark"></div>
    <div class="brand-text">
      <p class="brand-name">THE LINEN LOFT CO</p>
      <p class="brand-tagline">Folded with Quiet Care</p>
    </div>

    <div class="contact">
      <p class="person-name">Daniel Hart</p>
      <p class="person-role">President</p>
      <ul class="contact-list">
        <li class="contact-item">
          <span>020 7946 0321</span>
          <svg class="contact-icon" viewBox="0 0 24 24" aria-hidden="true"><path fill="var(--on-dark)" d="M6.6 2.5l3 3.4-1.9 2.6c1.3 2.9 3.6 5.2 6.5 6.6l2.6-1.9 3.4 3-1.6 3.4c-8.8-.3-15.9-7.4-16.2-16.2z"/></svg>
        </li>
        <li class="contact-item">
          <span>info@gentlelinenlofts.com</span>
          <svg class="contact-icon" viewBox="0 0 24 24" aria-hidden="true"><rect x="1" y="5" width="22" height="15" fill="var(--on-dark)"/><path d="M1.5 5.8l10.5 8 10.5-8" fill="none" stroke="var(--wave-black)" stroke-width="1.6"/></svg>
        </li>
        <li class="contact-item">
          <span>www.gentlelinenlofts.com</span>
          <svg class="contact-icon" viewBox="0 0 24 24" aria-hidden="true"><circle cx="12" cy="12" r="11" fill="var(--on-dark)"/><path d="M7 6c2 0 3 1 3 3s-2 2-2 4 2 2 2 4l-1 3c-3-1-5-4-5-8 0-2 1-4 3-6zM15 4c2 1 4 3 4 6-1 1-3 0-4-1s-2-3 0-5z" fill="var(--wave-black)"/></svg>
        </li>
      </ul>
      <p class="address">Linden Court, 42 Mill Lane, London N4 7QB</p>
    </div>
  </section>
</body>
</html>
```